Fernhale Business Card Design

We are looking for a fresh business card design for our new logo. We would like a business card that is unique but friendly. We are in the window coverings business offering blinds, shutters and shades for homes.

Target Market(s)

Targeting the end-consumer

Industry/Entity Type

Business

Requirements
Must have
• Must have a dedicates space for a photo of our sales person. Must contain our new logo (attached).

```html
<!DOCTYPE html>
<html lang="en">
<head>
<meta charset="utf-8">
<title>Fernhale Business Card</title>
<link rel="stylesheet" href="https://fonts.googleapis.com/css2?family=Source+Sans+3:wght@400;600;700&display=swap">
<style>
  :root {
    --backdrop: #e9e6e3;
    --slate: #5f6064;
    --leaf: #8cc63f;
    --leaf-dark: #6fa62a;
    --paper: #ffffff;
    --paper-shade: #ebebeb;
    --ink: #5d5e62;
    --photo-bg: #c9c8c3;
    --photo-fg: #3a3a3a;
  }
  * { box-sizing: border-box; margin: 0; padding: 0; }
  html, body { width: 1200px; height: 900px; overflow: hidden; }
  body {
    position: relative;
    background: var(--backdrop);
    font-family: "Source Sans 3", "Myriad Pro", sans-serif;
  }
  .card {
    position: absolute;
    overflow: hidden;
    box-shadow: 0 6px 18px rgba(0,0,0,0.18);
  }
  /* Contact side */
  .card-contact {
    left: 128px; top: 98px; width: 588px; height: 364px;
    background: var(--slate);
    color: var(--paper);
  }
  .accent-panel { position: absolute; left: 322px; top: 0; }
  .staff-photo {
    position: absolute; left: 33px; top: 30px; width: 119px; height: 138px;
    background: linear-gradient(180deg, var(--photo-bg), #bdbcb7);
  }
  .staff-name {
    position: absolute; left: 30px; top: 178px;
    font-size: 23px; font-weight: 600; letter-spacing: 0.1px;
  }
  .staff-role {
    position: absolute; left: 31px; top: 205px;
    font-size: 15.5px; font-weight: 400;
  }
  .contact-list {
    position: absolute; left: 30px; top: 251px;
    list-style: none; font-size: 15.5px; line-height: 21.5px;
  }
  .contact-list li { display: flex; align-items: center; gap: 7px; }
  .contact-list svg { width: 13px; height: 13px; fill: var(--paper); flex: none; }

  /* Brand side */
  .card-brand {
    left: 388px; top: 505px; width: 567px; height: 351px;
    background: linear-gradient(160deg, var(--paper) 0%, var(--paper) 40%, var(--paper-shade) 100%);
  }
  .brand-lockup {
    position: absolute; left: 106px; top: 136px;
    display: flex; align-items: center; gap: 18px;
  }
  .brand-square { width: 44px; height: 44px; background: var(--leaf); }
  .brand-name {
    font-size: 50px; font-weight: 600; color: var(--ink); letter-spacing: 0.5px; line-height: 1;
  }
  .brand-web {
    position: absolute; left: 0; right: 0; top: 293px; text-align: center;
    font-size: 15px; font-weight: 700; color: var(--ink);
  }
  .brand-web .highlight { color: var(--leaf-dark); }
</style>
</head>
<body>

<section class="card card-contact" aria-label="Business card, contact side">
  <svg class="accent-panel" width="266" height="364" viewBox="0 0 266 364" aria-hidden="true">
    <path d="M0 364 V70 A70 70 0 0 1 70 0 H266 V364 Z" fill="var(--paper)"/>
    <path d="M20 364 V80 A60 60 0 0 1 80 20 H266 V364 Z" fill="var(--leaf)"/>
  </svg>

  <div class="staff-photo" role="img" aria-label="Portrait photo of the sales person"></div>

  <h1 class="staff-name">Daniel Mercer</h1>
  <p class="staff-role">Managing Director</p>

  <ul class="contact-list">
    <li>
      <svg viewBox="0 0 16 16" aria-hidden="true"><path d="M4 0h8a1.5 1.5 0 0 1 1.5 1.5v13A1.5 1.5 0 0 1 12 16H4a1.5 1.5 0 0 1-1.5-1.5v-13A1.5 1.5 0 0 1 4 0zm0 2v10h8V2zm4 11a1 1 0 1 0 0 2 1 1 0 0 0 0-2z"/></svg>
      055-310 482 615
    </li>
    <li>
      <svg viewBox="0 0 16 16" aria-hidden="true"><path d="M1 5c0-2 3-3 7-3s7 1 7 3v1.5h-3.5V5h-7v1.5H1zM3 8l2-2h6l2 2v6H3zm5 1.3a2 2 0 1 0 0 4 2 2 0 0 0 0-4z"/></svg>
      055-310 482 615
    </li>
    <li>
      <svg viewBox="0 0 16 16" aria-hidden="true"><path d="M1 3h14v1.2L8 9 1 4.2zm0 2.7 7 4.8 7-4.8V13H1z"/></svg>
      hello@fernhale.com
    </li>
    <li>
      <svg viewBox="0 0 16 16" aria-hidden="true"><path d="M8 0a8 8 0 1 0 0 16A8 8 0 0 0 8 0zm-1 2.2c-.6 1-1 1.8-.5 2.6.6.8 2 .4 2.3 1.5.2 1-1.4 1.3-1.2 2.6.2 1.2 1.6 1.4 1.4 2.7-.1.9-.9 1.7-1.6 2.2A6 6 0 0 1 7 2.2zm4 1.4a6 6 0 0 1 2.8 6.8c-.6-.4-1.3-.8-1.7-1.6-.5-1 .4-1.8-.2-2.8-.5-.9-1.6-.9-1.6-1.6 0-.3.3-.6.7-.8z"/></svg>
      www.fernhaleshades.com
    </li>
  </ul>
</section>

<section class="card card-brand" aria-label="Business card, brand side">
  <div class="brand-lockup">
    <span class="brand-square" aria-hidden="true"></span>
    <span class="brand-name">Fernhale</span>
  </div>
  <p class="brand-web">www.<span class="highlight">fernhaleshades</span>.com</p>
</section>

</body>
</html>
```